New Book Cover Design Project for book about Trade Blend

DetWe need a book cover (front, back, spine) for a new book entitled ‘Trade Blend’’ and subtitled “beyond old rules toward real buyer wishes” (inverted commas not to be part of the title and subtitle). The author is Malcolm Ferrisby. The publisher is Tessellane Insights. The finished size of the paperback version will be 5" x 8" (127 x 203.2 mm). There will be paperback, hardback, and e-book versions. The final number of pages is expected to be in the region of 80 pages. Text for the back cover is in an attached document. At the bottom of the back cover should be publisher logo (rectangular) on the left and space for the ISBN bar code on the right. The design should be original and not include any stock images that have been created by someone else or may require obtaining a copyright licence to use. Symbols in common use and not copyrighted are probably ok. There are no required images, photographs or symbols except the publisher logo at the left bottom of the back cover. Spine lettering should be UK/US style with the top of the writing nearest the front cover. The designer is free to be creative using appropriate diagrams, symbols or abstract designs. A copy of the publisher logo is attached. Designers are assured that when evaluating designs absolutely no notice whatsoever is taken of a designer's Pixel Forum ranking or status; We are completely output driven, so what matters is the design, not the ranking or status of the designer. In a similar way, designs are not evaluated as 'good' or 'bad' - the winning design will be chosen after review by a design review panel and is not decided arbitrarily by a single person. All submitted designs should be capable of effective copyright assignment. Designs submitted for consideration should include front cover, spine, and back cover.
Candidate Trade Blend words that can be included in designs, if the designer wishes, include: product, place, promotion, price, consumer, company objectives, participants, physical evidence, process of service assembly, battery life, usability, security, fashion, design, brand, appearance, health, obedience, sustainability, accessibility, value, idea, information operation, beliefs, vectors.

Target Market(s)

Academics, teachers, text book writers, and students concerned with marketing.

Industry/Entity Type

Education

Font styles to use
Serif

Requirements
Must have
• • Author on the front cover and the spine. Templates have been added to the brief for the cover with spine for a 80 page book. There are .indd and .pdf templates that can be used. the .indd and .pdf templates show where the ISBN blocks should go. The other .PDF templates have the ISBN in the wrong place (middle of the lower back cover) but have more information about the meanings of template markings. Bleeds - PLEASE NOTE - the cover printing is not exact - there is minor variation when the printers print the covers. Therefore do not have solid blocks of colour that go to the edges of the spine or spine and cover pages with different blocks of colour - solid blocks of colour may go round the spine folds a little bit! See the templates - they indicate the areas for possible printing imprecision. The ISBN numbers in the template file names are what will be used - perfect is for the paperback and case is for the hardback.
Nice to have
• • It is not necessary to have the subtitle on the spine. The final book size may not be 80 pages, therefore the spine width may change, but not by much. • Use only standard fonts.
Should not have
• • Ideally, stock images should not be used as we cannot control other uses of images created by other sources, thus potentially damaging the book branding. I don't like solid black cover or spine backgrounds.

```html
<!DOCTYPE html>
<html lang="en">
<head>
<meta charset="utf-8">
<title>Trade Blend – Book Cover</title>
<link rel="stylesheet" href="https://fonts.googleapis.com/css2?family=Barlow+Condensed:wght@300;600;700&family=Source+Sans+3:wght@400;700&display=swap">
<style>
  :root {
    --stage: #2a2a2a;
    --sky-top: #b1cdef;
    --sky-bottom: #d8e7f8;
    --ink-grey: #5e646b;
    --ink-dark: #1b1b1b;
    --white: #ffffff;
    --emblem-light: #c9dbf2;
    --emblem-dark: #a7b6c8;
  }
  * { margin: 0; padding: 0; box-sizing: border-box; }
  html, body {
    width: 1042px; height: 1200px; overflow: hidden;
    background: var(--stage);
  }
  .cover-spread {
    position: absolute; left: 21px; top: 250px;
    width: 1000px; height: 700px;
    background: linear-gradient(180deg, var(--sky-top) 0%, var(--sky-bottom) 100%);
    overflow: hidden;
  }
  .condensed { font-family: "Barlow Condensed", "Arial Narrow", sans-serif; }

  /* Back cover: one flowing column so blocks never collide */
  .back-cover {
    position: absolute; left: 40px; top: 58px; width: 381px;
    display: flex; flex-direction: column; align-items: stretch;
  }
  .back-title {
    text-align: center; font-weight: 600; font-size: 46px; line-height: 1;
    color: var(--ink-grey); text-transform: uppercase;
  }
  .back-title .accent { color: var(--white); }
  .back-subtitle {
    margin-top: 2px;
    text-align: center; font-weight: 600; font-size: 20px; line-height: 1;
    color: var(--ink-grey); text-transform: uppercase; white-space: nowrap;
  }
  .blurb {
    margin-top: 9px;
    font-family: "Source Sans 3", "Myriad Pro", Arial, sans-serif;
    font-size: 13px; line-height: 17.3px;
    color: var(--ink-dark); text-align: justify; text-align-last: center;
  }
  .about-heading {
    margin-top: 12px;
    font-family: "Source Sans 3", "Myriad Pro", Arial, sans-serif;
    font-weight: 700; font-size: 15px; line-height: 18px;
    text-align: center; color: var(--ink-dark);
  }
  .about-row {
    margin-top: 7px;
    display: flex; gap: 9px; align-items: flex-start;
  }
  .author-photo {
    flex: 0 0 101px; height: 95px; margin-top: 2px;
    background: linear-gradient(160deg, #e9ece9 0%, #b7aca2 45%, #55585f 100%);
  }
  .author-bio {
    flex: 1;
    font-family: "Source Sans 3", "Myriad Pro", Arial, sans-serif;
    font-size: 13px; line-height: 17.2px;
    color: var(--ink-dark); text-align: justify;
  }

  /* Spine */
  .spine-title, .spine-author {
    position: absolute;
    writing-mode: vertical-rl; white-space: nowrap;
    color: var(--ink-grey); text-transform: uppercase; line-height: 1;
  }
  .spine-title { left: 480px; top: 46px; font-weight: 700; font-size: 42px; }
  .spine-title .accent { color: var(--white); }
  .spine-author { left: 484px; top: 423px; font-weight: 300; font-size: 34px; }

  /* Front cover */
  .front-series {
    position: absolute; left: 566px; top: 66px;
    writing-mode: vertical-rl; transform: rotate(180deg);
    font-weight: 700; font-size: 46px; line-height: 1; height: 205px;
    color: var(--ink-grey); text-transform: uppercase; text-align: center;
  }
  .front-title {
    position: absolute; left: 612px; top: 44px;
    font-weight: 700; font-size: 160px; line-height: 1;
    color: var(--white); text-transform: uppercase; letter-spacing: -2px;
  }
  .front-emblem {
    position: absolute; left: 711px; top: 292px; width: 252px; height: 252px;
  }
  .front-subtitle {
    position: absolute; left: 568px; top: 440px;
    font-weight: 600; font-size: 36px; line-height: 36px; white-space: nowrap;
    color: var(--ink-grey); text-transform: uppercase;
  }
  .front-author {
    position: absolute; left: 568px; top: 614px;
    font-weight: 300; font-size: 56px; line-height: 1; white-space: nowrap;
    color: var(--ink-grey); text-transform: uppercase;
  }
</style>
</head>
<body>
  <main class="cover-spread">
    <section class="back-cover">
      <h2 class="back-title condensed">Trade <span class="accent">Blend</span></h2>
      <p class="back-subtitle condensed">Beyond old rules toward real buyer wishes</p>
      <p class="blurb">This book has been inspired by the many textbooks, classes and student work about trade blend, which simply present or teach trade blend as 4Ps - very often not even acknowledging where those 4Ps came from. This approach is simply unacceptable academic work - no discussion of the extensive research from the 1920s onwards, about what is needed for effective marketing and trade blend. In several ways, this is a thoroughly radical book pushing against the common approach of simply teaching about simplistic 4Ps. Many students produce a trade blend for a company; they shouldn't. The book provides a solid example of what academics often call 'critical thinking'. Other ways in which the book is radical, is that it shows that trade blend is not only for products and services; it is also for ideas. The book discusses the idea that marketing can be seen as a branch of information warfare. Positioning should be included in trade blend considerations. Trade blend should not only be considered for legitimate products, services, and ideas; it is relevant also for those who trade in legal or mixed legal and illegal products and services. Examples are explored in the book.</p>
      <h3 class="about-heading">About Author</h3>
      <div class="about-row">
        <div class="author-photo" role="img" aria-label="Portrait photograph of the author"></div>
        <p class="author-bio">Malcolm Ferrisby has extensive experience in industry, academia, and a variety of NGOs working in human and civil rights. Within those contexts, he has a lot of marketing experience as practitioner, academic, and external examiner – contributing to the radical nature of this book.</p>
      </div>
    </section>

    <section class="spine">
      <p class="spine-title condensed">Trade <span class="accent">Blend</span></p>
      <p class="spine-author condensed">Malcolm Ferrisby</p>
    </section>

    <section class="front-cover">
      <p class="front-series condensed">Trade</p>
      <h1 class="front-title condensed">Blend</h1>
      <svg class="front-emblem" viewBox="0 0 252 252" role="img" aria-label="Abstract network sphere of connected grey nodes">
        <defs>
          <radialGradient id="emblem-fill" cx="50%" cy="50%" r="50%">
            <stop offset="0%" stop-color="var(--emblem-light)"/>
            <stop offset="100%" stop-color="var(--emblem-dark)"/>
          </radialGradient>
        </defs>
        <circle cx="126" cy="126" r="124" fill="url(#emblem-fill)"/>
      </svg>
      <p class="front-subtitle condensed">Beyond<br>old rules<br>toward real<br>buyer wishes</p>
      <p class="front-author condensed">Malcolm Ferrisby</p>
    </section>
  </main>
</body>
</html>
```